Business Card Design

New business card design

Target Market(s)

Residential & Commercial Property Managers

Industry/Entity Type

Plumbing Services

Contact Information for Business Card

Name - Rowan Keddle, title - Director, Phone Number - 0431 286 517, email - rowan@tbk-plumbing.com.au, Company ABN - 73 215 904 386,

Font styles to use
Sans Serif

Colors
0054AA
0677BA
7BADD7
CADEEF
E8F1F8

```html
<!DOCTYPE html>
<html lang="en">
<head>
<meta charset="utf-8">
<title>TBK Plumbing – Business Card</title>
<link rel="stylesheet" href="https://fonts.googleapis.com/css2?family=Montserrat:wght@300;400;600;700&display=swap">
<style>
  :root {
    --stage: #2b2b2c;
    --card-top: #232b36;
    --card-bottom: #1a2029;
    --accent: #2aa3e0;
    --accent-deep: #0677BA;
    --ink: #f2f5f8;
    --ink-soft: #cfd8e2;
    --muted: #5e6876;
  }
  * { margin: 0; padding: 0; box-sizing: border-box; }
  html, body { width: 1200px; height: 900px; overflow: hidden; }
  body {
    background: var(--stage);
    font-family: "Montserrat", sans-serif;
    position: relative;
  }
  .card {
    position: absolute;
    left: 267px;
    width: 665px;
    height: 380px;
    border-radius: 20px;
    background: linear-gradient(160deg, var(--card-top), var(--card-bottom));
    overflow: hidden;
    box-shadow: 0 14px 30px rgba(0,0,0,.45);
  }
  .card::after {
    content: "";
    position: absolute;
    left: 0; right: 0; bottom: 0;
    height: 9px;
    background: var(--accent);
  }
  .card--front { top: 40px; }
  .card--back { top: 480px; }

  .brand {
    display: flex;
    align-items: center;
    gap: 14px;
  }
  .brand__dot {
    width: 18px; height: 18px;
    border-radius: 50%;
    background: var(--accent);
  }
  .brand__name {
    font-weight: 300;
    letter-spacing: 2px;
  }
  .card--front .brand {
    position: absolute;
    left: 0; right: 0; top: 150px;
    justify-content: center;
  }
  .card--front .brand__name { font-size: 58px; color: #4a6890; }

  .card--back .brand {
    position: absolute;
    left: 44px; top: 46px;
  }
  .card--back .brand__name { font-size: 46px; color: var(--ink); }

  .holder {
    position: absolute;
    right: 46px; top: 44px;
    text-align: right;
  }
  .holder__name {
    font-weight: 700;
    font-size: 24px;
    color: var(--accent);
  }
  .holder__title {
    font-size: 14px;
    color: var(--ink);
    margin-top: 2px;
  }
  .holder-tab {
    position: absolute;
    right: 0; top: 44px;
    width: 22px; height: 38px;
    background: var(--accent);
  }

  .contact {
    position: absolute;
    left: 44px; bottom: 44px;
    color: var(--ink-soft);
    font-size: 15px;
    line-height: 1.55;
  }
  .contact__address { margin-bottom: 12px; }
  .contact__list { list-style: none; }
  .contact__item { display: flex; align-items: center; gap: 10px; }
  .contact__icon { width: 14px; height: 14px; flex: none; }
  .contact__abn { margin-top: 6px; }
  .contact__abn-label { color: var(--accent); font-weight: 600; }
</style>
</head>
<body>

<section class="card card--front" aria-label="Card front">
  <div class="brand">
    <span class="brand__dot"></span>
    <span class="brand__name">TBK Plumbing</span>
  </div>
</section>

<section class="card card--back" aria-label="Card back">
  <div class="brand">
    <span class="brand__dot"></span>
    <span class="brand__name">TBK Plumbing</span>
  </div>

  <div class="holder">
    <div class="holder__name">Rowan Keddle</div>
    <div class="holder__title">Director</div>
  </div>
  <span class="holder-tab"></span>

  <div class="contact">
    <p class="contact__address">48 Harbour Reach Road<br>Brackenfield, NSW 2310</p>
    <ul class="contact__list">
      <li class="contact__item">
        <svg class="contact__icon" viewBox="0 0 24 24" aria-hidden="true"><path fill="#2aa3e0" d="M6.6 10.8a15.1 15.1 0 0 0 6.6 6.6l2.2-2.2a1 1 0 0 1 1-.25 11.4 11.4 0 0 0 3.6.57 1 1 0 0 1 1 1V20a1 1 0 0 1-1 1A17 17 0 0 1 3 4a1 1 0 0 1 1-1h3.5a1 1 0 0 1 1 1c0 1.25.2 2.45.57 3.57a1 1 0 0 1-.25 1z"/></svg>
        0431 286 517
      </li>
      <li class="contact__item">
        <svg class="contact__icon" viewBox="0 0 24 24" aria-hidden="true"><path fill="#2aa3e0" d="M2 5h20v14H2z"/><path fill="none" stroke="#1f2630" stroke-width="2" d="M2 5l10 8 10-8"/></svg>
        rowan@tbk-plumbing.com.au
      </li>
      <li class="contact__item">
        <svg class="contact__icon" viewBox="0 0 24 24" aria-hidden="true"><circle cx="12" cy="12" r="10" fill="none" stroke="#2aa3e0" stroke-width="2"/><path fill="none" stroke="#2aa3e0" stroke-width="1.6" d="M2 12h20M12 2c3 3 3 17 0 20M12 2c-3 3-3 17 0 20"/></svg>
        www.tbk-plumbing.com.au
      </li>
    </ul>
    <p class="contact__abn"><span class="contact__abn-label">ABN</span> - 73 215 904 386</p>
  </div>
</section>

</body>
</html>
```